QVR business card

Need a business card for a company that provides instructional design and elearning development services. The website is here: http://quorvane.studio/

I'm attaching a current logo, as well as the old business card design. While I like to keep it clean, the old design is too simplistic for my liking. The only idea I want to reuse from the old design is placing industry jargon on the back of the card, just need a better way to present it. But if you have other ideas for the back--feel free to experiment.

Please use the colors complementary to the color we have on the website. Thank you!

```html
<!DOCTYPE html>
<html lang="en">
<head>
<meta charset="utf-8">
<title>QVR Business Card</title>
<link rel="stylesheet" href="https://fonts.googleapis.com/css2?family=Open+Sans:wght@400;600;700&display=swap">
<style>
  :root {
    --teal: #1bb3aa;
    --teal-deep: #12a39c;
    --gold: #d8cb8e;
    --sand: #e6d79c;
    --ink: #2b2b2b;
    --paper: #ffffff;
    --backdrop: #ececec;
    --map: rgba(31, 130, 120, 0.35);
  }
  * { box-sizing: border-box; margin: 0; padding: 0; }
  html, body { width: 1200px; height: 800px; overflow: hidden; }
  body {
    background: var(--backdrop);
    font-family: "Open Sans", Arial, sans-serif;
    position: relative;
  }
  .card {
    position: absolute;
    width: 540px;
    height: 310px;
    box-shadow: 0 6px 18px rgba(0,0,0,0.18);
    overflow: hidden;
  }

  /* Front */
  .card-front { left: 80px; top: 90px; background: var(--paper); }
  .card-front .bands { position: absolute; inset: 0; }
  .brand {
    position: absolute; left: 44px; top: 142px;
    display: flex; align-items: center; gap: 12px;
  }
  .brand-mark { width: 30px; height: 30px; background: var(--teal); }
  .brand-name {
    font-size: 40px; font-weight: 700; color: var(--gold); letter-spacing: 1px;
  }
  .contact {
    position: absolute; left: 310px; top: 36px;
    color: var(--ink);
  }
  .contact-name { color: var(--teal); font-weight: 700; font-size: 15px; }
  .contact-title { font-size: 11.5px; margin-bottom: 8px; }
  .contact-row {
    display: flex; align-items: center; gap: 8px;
    font-size: 11px; line-height: 19px;
  }
  .contact-row svg { width: 12px; height: 12px; fill: var(--teal); }

  /* Back */
  .card-back {
    left: 580px; top: 430px;
    background: linear-gradient(170deg, var(--teal) 0%, #8cc5a6 50%, var(--sand) 100%);
    color: var(--paper);
  }
  .world-map {
    position: absolute; left: 60px; top: 70px; width: 430px; height: 200px;
    background: var(--map); border-radius: 40px; opacity: 0.5;
  }
  .back-brand {
    position: absolute; left: 0; right: 0; top: 56px;
    text-align: center; font-size: 38px; font-weight: 700; color: var(--paper);
  }
  .services {
    position: absolute; left: 0; right: 0; top: 122px;
    display: flex; flex-direction: column; align-items: center; gap: 5px;
  }
  .service-tag {
    background: var(--teal-deep); color: var(--paper);
    font-size: 15px; padding: 1px 7px; border-radius: 2px; white-space: nowrap;
  }
  .back-url {
    position: absolute; left: 0; right: 0; top: 232px;
    text-align: center; font-size: 13px; letter-spacing: 0.3px;
  }
</style>
</head>
<body>

<section class="card card-front" aria-label="Business card front">
  <svg class="bands" viewBox="0 0 540 310" preserveAspectRatio="none" aria-hidden="true">
    <defs>
      <linearGradient id="band-fade" x1="0" x2="1">
        <stop offset="0" stop-color="#d8cb8e"/>
        <stop offset="1" stop-color="#1bb3aa"/>
      </linearGradient>
    </defs>
    <polygon points="0,290 250,290 290,200 540,200 540,212 298,212 258,302 0,302" fill="#d8cb8e"/>
    <polygon points="290,180 540,180 540,200 282,200" fill="url(#band-fade)"/>
    <polygon points="270,210 278,210 262,250 254,250" fill="#1bb3aa"/>
    <polygon points="282,210 290,210 274,250 266,250" fill="#d8cb8e"/>
  </svg>
  <div class="brand">
    <span class="brand-mark" aria-hidden="true"></span>
    <span class="brand-name">QVR</span>
  </div>
  <div class="contact">
    <p class="contact-name">Marian Castell</p>
    <p class="contact-title">Managing Director</p>
    <p class="contact-row">
      <svg viewBox="0 0 24 24" aria-hidden="true"><path d="M6.6 10.8a15 15 0 0 0 6.6 6.6l2.2-2.2a1 1 0 0 1 1-.25 11 11 0 0 0 3.6.6 1 1 0 0 1 1 1V20a1 1 0 0 1-1 1A17 17 0 0 1 3 4a1 1 0 0 1 1-1h3.5a1 1 0 0 1 1 1 11 11 0 0 0 .6 3.6 1 1 0 0 1-.25 1z"/></svg>
      555-014-2287
    </p>
    <p class="contact-row">
      <svg viewBox="0 0 24 24" aria-hidden="true"><path d="M2 5h20v14H2zm2 2v.5l8 5 8-5V7z"/></svg>
      mcastell@quorvane.studio
    </p>
    <p class="contact-row">
      <svg viewBox="0 0 24 24" aria-hidden="true"><path d="M12 2a10 10 0 1 0 0 20 10 10 0 0 0 0-20zm6.9 6h-3a15 15 0 0 0-1.3-3.9A8 8 0 0 1 18.9 8zM12 4c.8 1.2 1.5 2.5 1.9 4h-3.8c.4-1.5 1.1-2.8 1.9-4zM4.3 14a8 8 0 0 1 0-4h3.4a16 16 0 0 0 0 4zm.8 2h3a15 15 0 0 0 1.3 3.9A8 8 0 0 1 5.1 16zm3-8h-3a8 8 0 0 1 4.3-3.9A15 15 0 0 0 8.1 8zM12 20c-.8-1.2-1.5-2.5-1.9-4h3.8c-.4 1.5-1.1 2.8-1.9 4zm2.3-6H9.7a14 14 0 0 1 0-4h4.6a14 14 0 0 1 0 4zm.3 5.9a15 15 0 0 0 1.3-3.9h3a8 8 0 0 1-4.3 3.9zm1.7-5.9a16 16 0 0 0 0-4h3.4a8 8 0 0 1 0 4z"/></svg>
      www.quorvane.studio
    </p>
  </div>
</section>

<section class="card card-back" aria-label="Business card back">
  <div class="world-map" role="img" aria-label="Dotted world map in the background"></div>
  <p class="back-brand">QVR</p>
  <div class="services">
    <span class="service-tag">Instructional Design</span>
    <span class="service-tag">Elearning Development | Mobile Learning</span>
    <span class="service-tag">Insructor-LED Training</span>
  </div>
  <p class="back-url">www.quorvane.studio</p>
</section>

</body>
</html>
```